Business card design needed

I would like a one sided black business card with the information provided above. Refer to my website www.brightvolleyracquets.com.au for an example of colors I have used for my site, would like to keep this consistent for my business cards also, I will upload my logo below.

I am a new small business that provides tennis customers with racquet re stringing, tennis strings and accessories.

Industry/Entity Type

Small Business

Contact Information for Business Card

Bright Volley Tennis

Owen Whitby
Managing Director

brightvolleyracquets@mailbox.example
www.brightvolleyracquets.com.au
0491 726 305

Racquet Restringing/Tennis Strings/Accessories

Requirements
Must have
• Must have my logo and card must be black

```html
<!DOCTYPE html>
<html lang="en">
<head>
<meta charset="utf-8">
<title>Bright Volley Tennis – Business Cards</title>
<link rel="stylesheet" href="https://fonts.googleapis.com/css2?family=Arimo:wght@400;700&display=swap">
<style>
  :root {
    --backdrop: #e7e4df;
    --card-black: #000000;
    --lime: #b4d235;
    --white: #ffffff;
    --light-grey: #e6e6e6;
    --ink: #111111;
  }
  * { box-sizing: border-box; margin: 0; padding: 0; }
  html, body {
    width: 1200px;
    height: 475px;
    overflow: hidden;
    background: var(--backdrop);
    font-family: "Arimo", Arial, sans-serif;
  }
  .sheet {
    position: relative;
    width: 1200px;
    height: 475px;
  }
  .card {
    position: absolute;
    width: 547px;
    height: 313px;
    background: var(--card-black);
    border-radius: 13px;
    overflow: hidden;
  }
  .card--front { left: 31px; top: 81px; }
  .card--back  { left: 607px; top: 85px; }

  .brand {
    position: absolute;
    display: flex;
    align-items: center;
    gap: 10px;
    color: var(--lime);
    font-weight: 700;
    text-transform: uppercase;
    white-space: nowrap;
  }
  .brand__dot {
    width: 26px;
    height: 26px;
    border-radius: 50%;
    background: var(--lime);
    flex: none;
  }
  .card--front .brand { left: 50px; top: 64px; font-size: 25px; letter-spacing: 0.5px; }
  .card--back .brand {
    left: 0; right: 0; top: 112px;
    justify-content: center;
    font-size: 30px;
    letter-spacing: 0.5px;
  }
  .card--back .brand__dot { width: 30px; height: 30px; }

  .contact {
    position: absolute;
    left: 69px;
    top: 176px;
    list-style: none;
    color: var(--white);
    font-size: 14px;
    line-height: 18.5px;
  }
  .contact__phone { font-size: 15px; letter-spacing: 0.5px; }

  .name-band {
    position: absolute;
    left: 0; right: 0;
    top: 252px;
    height: 32px;
    background: var(--lime);
    display: flex;
    align-items: center;
    padding-left: 49px;
    color: var(--ink);
  }
  .name-band__name { font-size: 19.5px; letter-spacing: 0.3px; }
  .name-band__title { font-size: 13.5px; margin-left: 7px; padding-top: 4px; }

  .web-line {
    position: absolute;
    left: 0; right: 0;
    top: 240px;
    text-align: center;
    color: var(--light-grey);
    font-size: 13.5px;
    letter-spacing: 1.6px;
  }
</style>
</head>
<body>
  <main class="sheet">
    <section class="card card--front" aria-label="Business card front">
      <div class="brand"><span class="brand__dot"></span>Bright Volley Tennis</div>
      <ul class="contact">
        <li class="contact__phone">0491 726 305</li>
        <li class="contact__email">brightvolleyracquets@mailbox.example</li>
        <li class="contact__web">www.brightvolleyracquets.com.au</li>
      </ul>
      <div class="name-band">
        <span class="name-band__name">OWEN WHITBY,</span>
        <span class="name-band__title">Managing Director</span>
      </div>
    </section>

    <section class="card card--back" aria-label="Business card back">
      <div class="brand"><span class="brand__dot"></span>Bright Volley Tennis</div>
      <p class="web-line">www.brightvolleyracquets.com.au</p>
    </section>
  </main>
</body>
</html>
```